Marketing Flyer for Ashford Hollow Storage Climate Control Units

We are looking for a professional looking Marketing Flyer to advertise for our Climate Control Self Storage Units. Incorporate photos and our LOGO into the marketing flyer. See our website: AshfordHollowstorage.example
Updates

Marketing Flyer for our Self Storage Climate Control Units at Ashford Hollow Storage in Waynesville, NC

Want more designers to have a chance to submit entries.

Target Market(s)

Self Storage Facility Renters

Industry/Entity Type

Self Storage Facility

Font styles to use
Other font styles liked:
• Montserrat Font is what was used for our LOGO and would like to maintain consistency of Font on the Flyer

Colors
0054AA
0677BA
7BADD7
CADEEF
E8F1F8

Requirements
Must have
• Need to have LOGO in the Flyer and photos of the Climate Control Units

```html
<!DOCTYPE html>
<html lang="en">
<head>
<meta charset="utf-8">
<title>Ashford Hollow Storage – Flyer</title>
<link href="https://fonts.googleapis.com/css2?family=Montserrat:wght@400;500;600;700&display=swap" rel="stylesheet">
<style>
  :root {
    --navy: #1e1c5a;
    --white: #ffffff;
    --backdrop: #e9ebee;
    --sky: #7badd7;
    --sky-light: #cadeef;
    --brick: #a0644a;
    --foliage: #4f7a3c;
    --door-blue: #0054aa;
    --text: #1e1c5a;
  }
  * { box-sizing: border-box; margin: 0; padding: 0; }
  html, body { width: 1200px; height: 2824px; overflow: hidden; }
  body { background: var(--backdrop); font-family: "Montserrat", sans-serif; color: var(--text); position: relative; }

  .flyer {
    position: absolute; left: 40px; top: 623px;
    width: 1120px; height: 1578px;
    background: var(--white); overflow: hidden;
    box-shadow: 0 4px 18px rgba(0,0,0,.18);
  }
  .photo { position: absolute; }
  .photo-facility {
    left: 0; top: 0; width: 740px; height: 560px;
    background: linear-gradient(180deg, var(--sky) 0%, var(--sky-light) 32%, var(--foliage) 48%, var(--brick) 62%, #9a9a98 80%, #b3b3b0 100%);
    clip-path: polygon(0 0, 100% 0, 100% 76%, 0 98%);
  }
  .photo-entrance {
    left: 722px; top: 0; width: 398px; height: 640px;
    background: linear-gradient(180deg, #3b4a6a 0%, #2c4a8a 10%, #9b5a40 22%, #b06c4e 60%, #8c5844 80%, #a9a9a6 100%);
    clip-path: polygon(18% 0, 100% 0, 100% 100%, 0 100%, 0 22%);
  }
  .photo-divider { position: absolute; left: 0; top: 0; width: 1120px; height: 700px; }

  .logo-box {
    position: absolute; left: 54px; top: 0; width: 338px; height: 226px;
    background: var(--white);
    display: flex; flex-direction: column; align-items: center; justify-content: center;
    text-align: center; color: var(--navy); font-weight: 600;
  }
  .logo-name { font-size: 31px; letter-spacing: .5px; line-height: 1.15; }
  .logo-sub { font-size: 19px; letter-spacing: 6px; margin-top: 4px; }

  .features-panel {
    position: absolute; left: 639px; top: 655px; width: 421px; height: 668px;
    background: var(--navy); color: var(--white);
    padding: 142px 24px 0 24px;
  }
  .features-panel h2 { font-size: 25px; font-weight: 600; margin-bottom: 14px; }
  .features-panel p { font-size: 16.5px; line-height: 20px; text-align: justify; margin-bottom: 10px; }
  .amenities { list-style: none; padding-left: 16px; }
  .amenities li { font-size: 17px; font-weight: 600; line-height: 30px; }
  .amenities li::before { content: "•"; margin-right: 10px; }

  .hex-layer { position: absolute; left: 0; top: 0; width: 1120px; height: 900px; }

  .content {
    position: absolute; left: 36px; top: 618px; width: 560px;
  }
  .content h2 { font-size: 25px; font-weight: 600; line-height: 28px; margin-bottom: 12px; }
  .content p { font-size: 16.8px; line-height: 20.2px; text-align: justify; margin-bottom: 22px; }

  .contact {
    position: absolute; left: 650px; top: 1340px; width: 400px; text-align: center; color: var(--navy);
  }
  .contact-name { font-size: 29px; font-weight: 600; margin-bottom: 8px; }
  .contact-address { font-size: 22px; font-weight: 500; line-height: 30px; }
  .contact-phone { font-size: 49px; font-weight: 600; margin-top: 22px; }

  .footer-band { position: absolute; left: 0; bottom: 0; width: 1120px; height: 9px; background: var(--navy); }
</style>
</head>
<body>
  <main class="flyer">
    <div class="photo photo-facility" role="img" aria-label="Photo of the brick storage facility with sign post and parking lot"></div>
    <div class="photo photo-entrance" role="img" aria-label="Photo of the brick office entrance with glass door and bench"></div>
    <svg class="photo-divider" viewBox="0 0 1120 700" aria-hidden="true">
      <line x1="792" y1="0" x2="722" y2="140" stroke="#ffffff" stroke-width="8"/>
    </svg>

    <div class="logo-box">
      <div class="logo-name">ASHFORD HOLLOW</div>
      <div class="logo-sub">STORAGE</div>
    </div>

    <section class="features-panel">
      <h2>Features &amp; Amenities</h2>
      <p>Every storage feature is designed from scratch against standards forged from years of experience in the self storage industry. The result is a high quality consistent customer experience you can count on.</p>
      <ul class="amenities">
        <li>24/7 Access</li>
        <li>All Major Credit Cards Accepted</li>
        <li>Auto Pay</li>
        <li>Climate Controlled Units</li>
        <li>Contactless Rental and Payment</li>
        <li>Covered Vehicle / Boat / RV Parking</li>
        <li>Drive Up Access</li>
        <li>Drive-Up Units</li>
        <li>Ground Floor Units</li>
        <li>Outdoor Parking</li>
        <li>Phone Support</li>
        <li>Trailer Storage</li>
      </ul>
    </section>

    <svg class="hex-layer" viewBox="0 0 1120 900">
      <defs>
        <linearGradient id="hallwayTone" x1="0" y1="0" x2="1" y2="0">
          <stop offset="0" stop-color="#1f3f8f"/>
          <stop offset="0.4" stop-color="#c9ccd2"/>
          <stop offset="0.6" stop-color="#c9ccd2"/>
          <stop offset="1" stop-color="#1f3f8f"/>
        </linearGradient>
        <linearGradient id="doorTone" x1="0" y1="0" x2="1" y2="1">
          <stop offset="0" stop-color="#2a5bb5"/>
          <stop offset="1" stop-color="#133a86"/>
        </linearGradient>
      </defs>
      <!-- hallway hexagon -->
      <polygon points="618,364 768,451 768,625 618,712 468,625 468,451" fill="none" stroke="#1e1c5a" stroke-width="1.5"/>
      <polygon points="618,372 761,455 761,621 618,704 475,621 475,455" fill="#ffffff"/>
      <polygon points="618,384 751,461 751,615 618,692 485,615 485,461" fill="url(#hallwayTone)" role="img" aria-label="Photo of an indoor hallway lined with blue roll-up unit doors"/>
      <!-- door hexagon -->
      <polygon points="920,420 1078,511 1078,693 920,784 762,693 762,511" fill="none" stroke="#1e1c5a" stroke-width="1.5"/>
      <polygon points="920,428 1071,515 1071,689 920,776 769,689 769,515" fill="#ffffff"/>
      <polygon points="920,442 1059,522 1059,682 920,762 781,682 781,522" fill="url(#doorTone)" role="img" aria-label="Photo of a blue roll-up storage unit door"/>
    </svg>

    <article class="content">
      <h2>Storage Units and Vehicle<br>Storage in Waynesville, NC</h2>
      <p>When you need a bit more room for all the items you need for your household or business, Ashford Hollow Storage, powered by Birchline Storage Management, can help you get some square footage. Our convenient Waynesville self-storage facility is located on Linden Street, near Maple Avenue. Along with a variety of storage unit sizes and features, we even offer outdoor parking storage, suitable for keeping your extra recreational vehicles in between Smoky Mountain adventures, lake trips, family road trips, and more.</p>

      <h2>Waynesville Storage Facility Near Maple Avenue</h2>
      <p>Our self-storage in Waynesville, NC, is located conveniently close to Maple Avenue, allowing for hassle-free navigation to your storage space. We’re also close to many of your other necessary stops around town, including PartsDepot, Ridgeway Bank, Summit Credit Union, Marco’s Family Pizza &amp; Pasta Restaurant, Keller Auto Parts, and the Laurel Plaza shopping center. Whether you’re looking for a storage unit to supplement the space in your living or working space, you’ll find Ashford Hollow Storage nearby.</p>

      <h2>Drive-Up Access Storage in Waynesville</h2>
      <p>Choose one of our drive-up storage units and store even your largest items with ease! With drive-up access storage, you’ll be able to pull your personal or moving vehicles directly up to your Waynesville self-storage unit and get your items moved in or out with ease. Have lighter items that you just need to access as quickly as possible? Drive-up storage units are still a great choice!</p>

      <h2>Waynesville Climate-Controlled Storage</h2>
      <p>Ashford Hollow Storage is adding new climate-controlled storage units in the summer of 2023. With the variable North Carolina weather, climate-controlled storage is a great option for keeping your sensitive belongings like files and furniture away from the elements. This is especially important when storing items long-term through seasonal changes. Our climate-controlled storage units are conveniently available in several sizes to help meet all of your storage needs.</p>
    </article>

    <address class="contact" style="font-style:normal">
      <div class="contact-name">Ashford Hollow Storage</div>
      <div class="contact-address">412 West Linden St,<br>Waynesville, NC 28786</div>
      <div class="contact-phone">(828) 555-0142</div>
    </address>

    <div class="footer-band"></div>
  </main>
</body>
</html>
```